Simple Logo Design for Semi-Clear Plastic Frosted Card stock

Create a business card on frosted plastic. compliment existing logo elements with a tree trunk, roots, or seed at the lower half and the full logo both on the front.

Contact information will go on a solid portion of the back of this design since this card stock is semi-transparent.

It is important to consider this plastic card stock medium in your design. I found helpful tips and guides listed at vellaprint-sample.net: be careful to understand ink printed on plastic cards cannot have too much of a consistent print area or risks peeling and fine lines can easily scratch off.
Updates

2" x 3.5" 20PT Clear Plastic Business cards with Round corners Please get info or templates here: https://www.vellaprint-sample.net/product-detail/2-x-35-20pt-clear-plastic-business-cards-with-round-corners

Target Market(s)

Not for profit- religion

Industry/Entity Type

Business

Must include complementary elements to the existing logo

Font styles to use
Decorative

Colors
000000

Requirements
Must have
• Elements of community, nature and oneness. Such as: seed, roots, tree trunk, etc.
• Three lines of space on the back for Name, Title, Phone Number.
Nice to have
• I like a light use of decorative elements
Should not have
• No eyes, from faces or animals.

```html
<!DOCTYPE html>
<html lang="en">
<head>
<meta charset="utf-8">
<title>Grovewell – Business Card</title>
<link href="https://fonts.googleapis.com/css2?family=Questrial&family=Source+Sans+3:wght@400;600&display=swap" rel="stylesheet">
<style>
  :root {
    --backdrop: #e8e3df;
    --frost: #f3f1ef;
    --frost-edge: #e4e0dd;
    --card-white: #ffffff;
    --leaf-green: #4a9a42;
    --teal: #1f6b63;
    --tagline: #3f4a48;
    --on-green: #ffffff;
  }
  * { margin: 0; padding: 0; box-sizing: border-box; }
  html, body {
    width: 1200px;
    height: 900px;
    overflow: hidden;
    background: var(--backdrop);
  }
  .canvas {
    position: relative;
    width: 1200px;
    height: 900px;
  }
  .card {
    position: absolute;
    width: 556px;
    height: 344px;
    overflow: hidden;
    box-shadow: 0 6px 18px rgba(0,0,0,0.12);
  }
  .card--back {
    left: 238px;
    top: 62px;
    background: linear-gradient(180deg, var(--frost) 0%, var(--frost-edge) 100%);
  }
  .card--front {
    left: 457px;
    top: 518px;
    width: 560px;
    background: var(--card-white);
  }
  .brand {
    position: absolute;
    left: 0;
    width: 100%;
    display: flex;
    flex-direction: column;
    align-items: center;
  }
  .card--back .brand { top: 26px; }
  .card--front .brand { top: 86px; }
  .brand__mark {
    border-radius: 50%;
    background: var(--teal);
  }
  .card--back .brand__mark { width: 80px; height: 80px; margin-bottom: 10px; }
  .card--front .brand__mark { width: 96px; height: 96px; margin-bottom: 18px; }
  .brand__name {
    font-family: "Questrial", sans-serif;
    font-weight: 400;
    letter-spacing: 2px;
    line-height: 1;
    color: var(--teal);
    text-transform: uppercase;
  }
  .card--back .brand__name { font-size: 32px; }
  .card--front .brand__name { font-size: 36px; }
  .brand__tagline {
    margin-top: 5px;
    font-family: "Questrial", sans-serif;
    letter-spacing: 1px;
    line-height: 1.1;
    color: var(--tagline);
    text-transform: uppercase;
  }
  .card--back .brand__tagline { font-size: 11.5px; }
  .card--front .brand__tagline { font-size: 12.5px; }
  .contact-band {
    position: absolute;
    left: 0;
    top: 196px;
    width: 100%;
    height: 148px;
    background: var(--leaf-green);
    color: var(--on-green);
    font-family: "Source Sans 3", sans-serif;
    text-align: center;
  }
  .contact-band__name {
    margin-top: 26px;
    font-weight: 600;
    font-size: 22px;
    line-height: 1.2;
  }
  .contact-band__title {
    margin-top: 6px;
    font-size: 17px;
  }
  .contact-band__phone {
    margin-top: 14px;
    font-size: 19px;
    display: inline-flex;
    align-items: center;
    gap: 6px;
  }
  .contact-band__phone svg { width: 14px; height: 14px; fill: var(--on-green); }
</style>
</head>
<body>
<main class="canvas">

  <section class="card card--back" aria-label="Card back">
    <div class="brand">
      <div class="brand__mark" aria-hidden="true"></div>
      <div class="brand__name">Grovewell</div>
      <div class="brand__tagline">Learning, Fellowship &amp; Calm</div>
    </div>
    <div class="contact-band">
      <p class="contact-band__name">Daniel Hartley</p>
      <p class="contact-band__title">Managing Director</p>
      <p class="contact-band__phone">
        <svg viewBox="0 0 24 24" aria-hidden="true"><path d="M6.6 10.8a15.1 15.1 0 0 0 6.6 6.6l2.2-2.2a1 1 0 0 1 1-.25 11.4 11.4 0 0 0 3.6.57 1 1 0 0 1 1 1V20a1 1 0 0 1-1 1A17 17 0 0 1 3 4a1 1 0 0 1 1-1h3.5a1 1 0 0 1 1 1c0 1.250.2 2.460.57 3.6a1 1 0 0 1-.25 1z"/></svg>
        044-987 654 321
      </p>
    </div>
  </section>

  <section class="card card--front" aria-label="Card front">
    <div class="brand">
      <div class="brand__mark" aria-hidden="true"></div>
      <div class="brand__name">Grovewell</div>
      <div class="brand__tagline">Learning, Fellowship &amp; Calm</div>
    </div>
  </section>

</main>
</body>
</html>
```